BOLD & MINIMALIST DESIGN NEEDED

We want a very bold but minimalistic business card design that is impactful and utilizes both sides of the business card. Our current logo is included for your use.

We want bold fonts and good use of negative space. We don't want the logo to overpower the design.

Target Market(s)

Professionals who are building new commercial buildings.

Industry/Entity Type

Construction

Contact Information for Business Card

Name, Title, email, office phone, cell phone, website

Font styles to use
Serif
Sans Serif

Requirements
Must have
• Bold design!

```html
<!DOCTYPE html>
<html lang="en">
<head>
<meta charset="utf-8">
<title>Ridgeway Design + Build — Business Card</title>
<link rel="stylesheet" href="https://fonts.googleapis.com/css2?family=Montserrat:wght@400;500;700;800&display=swap">
<style>
  :root {
    --backdrop: #dcdcdc;
    --paper: #ffffff;
    --ink: #0b0c0e;
    --green: #7cc243;
    --green-light: #9bd15f;
    --grey-text: #6b6b6b;
  }
  * { box-sizing: border-box; margin: 0; padding: 0; }
  html, body {
    width: 1200px; height: 1200px; overflow: hidden;
    background: var(--backdrop);
    font-family: "Montserrat", Arial, sans-serif;
  }
  .card {
    position: absolute; left: 179px; width: 861px; height: 496px;
    background: var(--paper); overflow: hidden;
  }
  .card--front { top: 84px; }
  .card--back { top: 622px; }

  .brand {
    position: absolute; display: flex; align-items: center; gap: 16px;
    font-weight: 800; text-transform: uppercase; line-height: 1;
  }
  .brand__mark { width: 34px; height: 34px; background: var(--green); flex: none; }
  .brand__text { display: flex; flex-direction: column; align-items: center; }
  .brand__name { font-size: 52px; letter-spacing: 1px; }
  .brand__tag { font-size: 17px; letter-spacing: 7px; margin-top: 8px; }

  .card--front .brand { left: 50%; top: 50%; transform: translate(-50%, -50%); color: var(--ink); }

  .card__shapes { position: absolute; inset: 0; width: 100%; height: 100%; }

  .person { position: absolute; left: 29px; top: 36px; }
  .person__name { font-size: 38px; font-weight: 700; color: var(--ink); letter-spacing: 0.5px; }
  .person__title { font-size: 29px; font-weight: 400; color: var(--green); letter-spacing: 1px; margin-top: 2px; }

  .contacts { position: absolute; left: 29px; top: 200px; list-style: none; }
  .contacts li {
    display: flex; align-items: center; gap: 12px; height: 35px;
    font-size: 22px; color: var(--grey-text); letter-spacing: 1px;
  }
  .contacts svg { width: 25px; height: 25px; flex: none; }
  .contacts .accent { color: var(--green); }

  .card--back .brand { left: 641px; top: 418px; transform: translate(-50%, -50%); color: var(--paper); }
  .card--back .brand__name { font-size: 46px; }
  .card--back .brand__tag { font-size: 15px; letter-spacing: 6px; }
</style>
</head>
<body>

<section class="card card--front">
  <div class="brand">
    <span class="brand__mark"></span>
    <span class="brand__text">
      <span class="brand__name">Ridgeway</span>
      <span class="brand__tag">Design + Build</span>
    </span>
  </div>
</section>

<section class="card card--back">
  <svg class="card__shapes" viewBox="0 0 1387 797" preserveAspectRatio="none" aria-hidden="true">
    <polygon points="0,546 312,676 1305,168 312,712 0,558" fill="var(--green-light)"/>
    <polygon points="0,566 312,724 1387,133 1387,797 0,797" fill="var(--ink)"/>
  </svg>

  <div class="person">
    <h1 class="person__name">Name Surename</h1>
    <p class="person__title">Director</p>
  </div>

  <ul class="contacts">
    <li>
      <svg viewBox="0 0 24 24"><path fill="var(--ink)" d="M6.6 10.8a15 15 0 0 0 6.6 6.6l2.2-2.2a1 1 0 0 1 1-.25 11.4 11.4 0 0 0 3.6.57 1 1 0 0 1 1 1V20a1 1 0 0 1-1 1A17 17 0 0 1 3 4a1 1 0 0 1 1-1h3.5a1 1 0 0 1 1 1c0 1.25.2 2.45.57 3.57a1 1 0 0 1-.25 1z"/><path fill="none" stroke="var(--ink)" stroke-width="1.6" d="M14 6a5 5 0 0 1 4 4M14 2a9 9 0 0 1 8 8"/></svg>
      555-014-2200
    </li>
    <li>
      <svg viewBox="0 0 24 24"><path fill="var(--ink)" d="M2 8c0-3 20-3 20 0v2h-5V8H7v2H2zM6 12l2-2h8l2 2 2 9H4zm6 2a2.5 2.5 0 1 0 0 5 2.5 2.5 0 0 0 0-5z"/></svg>
      555-014-2200
    </li>
    <li>
      <svg viewBox="0 0 24 24"><rect x="2" y="5" width="20" height="14" fill="none" stroke="var(--ink)" stroke-width="2"/><path d="M2 5l10 8 10-8M2 19l7-7M22 19l-7-7" fill="none" stroke="var(--ink)" stroke-width="1.6"/></svg>
      info@r-d-b.com
    </li>
    <li>
      <svg viewBox="0 0 24 24" fill="none" stroke="var(--ink)" stroke-width="1.5"><circle cx="12" cy="12" r="10"/><ellipse cx="12" cy="12" rx="4.5" ry="10"/><path d="M2 12h20M3.5 7h17M3.5 17h17M12 2v20"/></svg>
      <span>www.<span class="accent">r-d-b</span>.com</span>
    </li>
  </ul>

  <div class="brand">
    <span class="brand__mark"></span>
    <span class="brand__text">
      <span class="brand__name">Ridgeway</span>
      <span class="brand__tag">Design + Build</span>
    </span>
  </div>
</section>

</body>
</html>
```